Business Cards Design for the electrical wholesaler: clean bold dynamic :)

We need a business card design that would follow our latest brand guidelines. As an electrical wholesaler we want to bring a fresh look and feel into the industry. The design should be clean bold and dynamic. It should come alive with the renewed energy of our green colour. Our grey colour should keep things balanced and complement the notion of maturity and responsibility. We employ Lato as a corporate font however are not bound by this font and we’re open to interpretation here.

Target Market(s)

Electrical contractors

Industry/Entity Type

Business

Contact Information for Business Card

Logo
Name & Surname: Halyna Dorosh
Job Title: Director of Marketing
Email: halya.dorosh@quillmail.example
Cell phone: XXX.XXX.XXXX
Address: 20517 - 87 Ave. Edmonton, AB, Canada. T6K 4N8
Business Phone: 780.555.0184
Website: www.brovix.example

Font styles to use
Other font styles liked:
• Lato

Requirements
Must have
• Logo & website
Nice to have
• Brand elements - some of them you may find in the attached Brand Guidelines (e.g. three lines on the background signifying "W")

```html
<!DOCTYPE html>
<html lang="en">
<head>
<meta charset="utf-8">
<title>Brovix business card</title>
<link href="https://fonts.googleapis.com/css2?family=Lato:wght@400;700&display=swap" rel="stylesheet">
<style>
  :root {
    --green: #8cc63f;
    --grey: #4d4d4f;
    --grey-text: #555659;
    --rule: #b5b5b5;
    --card-dark: #2b2b2b;
    --card-light: #ffffff;
    --backdrop: #e4e4e4;
  }
  * { margin: 0; padding: 0; box-sizing: border-box; }
  html, body {
    width: 1200px; height: 1134px; overflow: hidden;
    background: var(--backdrop);
    font-family: "Lato", sans-serif;
  }
  .canvas { position: relative; width: 1200px; height: 1134px; }
  .card {
    position: absolute; top: 252px; width: 399px; height: 672px;
    border-radius: 14px; overflow: hidden;
  }
  .card--back { left: 197px; background: var(--card-dark); }
  .card--front { left: 658px; background: var(--card-light); }

  .brand {
    position: absolute; display: flex; align-items: center; gap: 12px;
    font-weight: 400; letter-spacing: -1px; line-height: 1;
  }
  .brand__dot { width: 46px; height: 46px; border-radius: 50%; background: var(--green); flex: none; }
  .card--back .brand { left: 0; right: 0; top: 308px; justify-content: center; font-size: 58px; color: #ffffff; }
  .card--back .brand__dot { width: 40px; height: 40px; }
  .card--front .brand { left: 43px; top: 128px; font-size: 66px; color: var(--grey); }

  .person { position: absolute; left: 74px; top: 366px; }
  .person__name { font-size: 31px; font-weight: 700; color: var(--green); line-height: 1.05; }
  .person__title { font-size: 19px; color: var(--grey-text); margin-top: 2px; }

  .rule { position: absolute; left: 74px; width: 218px; height: 2px; background: var(--rule); }
  .rule--one { top: 446px; }
  .rule--two { top: 498px; }

  .address { position: absolute; left: 74px; top: 466px; font-size: 15.5px; line-height: 23px; color: var(--grey-text); }
  .card--front .person { left: 74px; top: 368px; }
  .card--front .person, .card--front .address, .card--front .rule { left: 74px; }

  .contacts { position: absolute; left: 74px; top: 519px; list-style: none; }
  .contacts li { display: flex; align-items: center; height: 23px; font-size: 15.5px; color: var(--grey-text); }
  .contacts svg { width: 14px; height: 14px; margin-right: 10px; fill: var(--green); flex: none; }
</style>
</head>
<body>
<main class="canvas">
  <section class="card card--back" role="img" aria-label="Dark card back with faint repeating brand pattern">
    <div class="brand"><span class="brand__dot"></span><span>brovix</span></div>
  </section>

  <section class="card card--front">
    <div class="brand"><span class="brand__dot"></span><span>brovix</span></div>

    <div class="person" style="left:74px">
      <p class="person__name">Halyna Dorosh</p>
      <p class="person__title">Director of Marketing</p>
    </div>
    <div class="rule" style="top:446px"></div>
    <p class="address" style="top:465px">20517 - 87 Ave. Edmonton<br>AB, Canada. T6K 4N8</p>
    <div class="rule" style="top:528px"></div>

    <ul class="contacts" style="top:548px">
      <li><svg viewBox="0 0 14 14"><path d="M3.5 0h7a1 1 0 0 1 1 1v12a1 1 0 0 1-1 1h-7a1 1 0 0 1-1-1V1a1 1 0 0 1 1-1zm.6 1.5v9.5h5.8V1.5zM7 11.6a.8.8 0 1 0 0 1.6.8.8 0 0 0 0-1.6z"/></svg>780.555.0184</li>
      <li><svg viewBox="0 0 14 14"><path d="M3 .5l2.2 2.8-1.3 1.8c.9 1.9 2.4 3.5 4.4 4.5l1.7-1.3 2.9 2.1-1.2 2.6C6.3 12.8 1.2 7.7.4 2z"/></svg>780.555.0184</li>
      <li><svg viewBox="0 0 14 14"><path d="M0 3h14v1L7 8.3 0 4zm0 2.6l7 4.2 7-4.2V12H0z"/></svg>halya.dorosh@quillmail.example</li>
      <li><svg viewBox="0 0 14 14"><path d="M7 0a7 7 0 1 0 0 14A7 7 0 0 0 7 0zm4.9 6.3H9.8A11 11 0 0 0 8.9 1.7a5.6 5.6 0 0 1 3 4.6zM7 1.5c.7.9 1.3 2.6 1.4 4.8H5.6C5.7 4.1 6.3 2.4 7 1.5zM5.1 1.7a11 11 0 0 0-.9 4.6H2.1a5.6 5.6 0 0 1 3-4.6zM2.1 7.7h2.1c.1 1.8.4 3.4.9 4.6a5.6 5.6 0 0 1-3-4.6zM7 12.5c-.7-.9-1.3-2.6-1.4-4.8h2.8c-.1 2.2-.7 3.9-1.4 4.8zm1.9-.2c.5-1.2.8-2.8.9-4.6h2.1a5.6 5.6 0 0 1-3 4.6z"/></svg>www.brovix.example</li>
    </ul>
  </section>
</main>
</body>
</html>
```